New Innovative Counselling and psychotherapy Service needs Business Card design

Keep it simple and professional. On one side, just company name and logo (perhaps in all blue) and maybe a tag line.

On other side (all white) my name and Qualifications in centre

Industry/Entity Type

Health And Wellness

Contact Information for Business Card

Dara Whelby
Counsellor & Psychotherapist
BSc (Psychol.), BA, Dip. (Couns. & Psych.), PG.Cert (CBT), FGTrK, ONRE

I will also require Mobile no, Email and web site address of which I'll pass on to final designer.

Font styles to use
Sans Serif

Requirements
Must have
• My Logo Only and please use the colours in logo that is in it.
Should not have
• Any other images

```html
<!DOCTYPE html>
<html lang="en">
<head>
<meta charset="utf-8">
<title>Harbour Lane – Business Card</title>
<link rel="stylesheet" href="https://fonts.googleapis.com/css2?family=Roboto:wght@300;400;500;700&display=swap">
<style>
  :root {
    --sky: #4fb6ea;
    --sky-deep: #3fa6df;
    --leaf: #7cc24a;
    --ink: #2b2b2b;
    --paper: #ffffff;
    --canvas: #e6e8ea;
  }
  * { margin: 0; padding: 0; box-sizing: border-box; }
  html, body {
    width: 1200px; height: 726px; overflow: hidden;
    background: var(--canvas);
    font-family: "Roboto", Arial, sans-serif;
  }
  .sheet {
    width: 1200px; height: 726px;
    display: flex; align-items: center; justify-content: center; gap: 40px;
  }
  .card {
    position: relative;
    width: 540px; height: 310px;
    overflow: hidden;
    box-shadow: 0 6px 18px rgba(0,0,0,.12);
  }

  /* Front */
  .card--front { background: var(--sky); color: var(--paper); }
  .front-brand {
    position: absolute; left: 0; right: 0; top: 112px;
    display: flex; align-items: center; justify-content: center; gap: 16px;
  }
  .brand-dot {
    width: 54px; height: 54px; border-radius: 50%;
    background: var(--paper);
  }
  .front-text { display: flex; flex-direction: column; }
  .brand-name {
    font-weight: 300; font-size: 40px; letter-spacing: .5px; line-height: 1;
  }
  .tagline {
    margin-top: 8px;
    font-weight: 300; font-size: 14px; letter-spacing: 7px;
  }

  /* Back */
  .card--back { background: var(--paper); }
  .accent-area {
    position: absolute; left: 300px; right: 0; top: 100px; bottom: 0;
    background: linear-gradient(165deg, var(--leaf) 0, var(--sky) 22%, var(--sky-deep) 100%);
  }
  .back-brand {
    position: absolute; left: 70px; top: 56px;
    display: flex; align-items: center; gap: 16px;
    color: var(--ink);
  }
  .back-brand .brand-dot { background: var(--sky-deep); width: 48px; height: 48px; }
  .back-brand .brand-name { font-size: 38px; }
  .holder {
    position: absolute; left: 36px; top: 150px;
    color: var(--ink);
  }
  .holder-name {
    font-weight: 700; font-size: 22px; color: var(--sky-deep); margin-bottom: 4px;
  }
  .holder-line { font-size: 12px; line-height: 1.35; }
  .contacts {
    position: absolute; right: 22px; top: 172px;
    list-style: none; color: var(--paper);
    font-size: 13px; line-height: 1.65; text-align: right;
  }
  .contacts li { display: flex; align-items: center; justify-content: flex-end; gap: 8px; }
  .contacts svg { width: 12px; height: 12px; fill: var(--paper); flex: none; }
</style>
</head>
<body>
<main class="sheet">

  <section class="card card--front" aria-label="Card front">
    <div class="front-brand">
      <span class="brand-dot"></span>
      <div class="front-text">
        <span class="brand-name">Harbour Lane</span>
        <span class="tagline">A tag line goes here</span>
      </div>
    </div>
  </section>

  <section class="card card--back" aria-label="Card back">
    <div class="accent-area" role="img" aria-label="Decorative blue and green wave artwork"></div>

    <div class="back-brand">
      <span class="brand-dot"></span>
      <span class="brand-name">Harbour Lane</span>
    </div>

    <div class="holder">
      <p class="holder-name">Dara Whelby</p>
      <p class="holder-line">Counsellor &amp; Psychotherapist</p>
      <p class="holder-line">BSc (Psychol.), BA, Dip. (Couns. &amp; Psych.),</p>
      <p class="holder-line">PG.Cert (CBT), FGTrK, ONRE</p>
    </div>

    <ul class="contacts">
      <li>5550 123 4567
        <svg viewBox="0 0 24 24" aria-hidden="true"><path d="M6.6 10.8a15.1 15.1 0 0 0 6.6 6.6l2.2-2.2c.3-.3.7-.4 1-.2 1.1.4 2.3.6 3.6.6.6 0 1 .4 1 1V20c0 .6-.4 1-1 1A17 17 0 0 1 3 4c0-.6.4-1 1-1h3.5c.6 0 1 .4 1 1 0 1.3.2 2.5.6 3.6.1.3 0 .7-.2 1z"/></svg>
      </li>
      <li>www.HarbourLane.com
        <svg viewBox="0 0 24 24" aria-hidden="true"><path d="M2 5h20v14H2zm2 2v.5l8 5 8-5V7zm0 2.8V17h16V9.8l-8 5z"/></svg>
      </li>
      <li>dara.w@HarbourLane.com
        <svg viewBox="0 0 24 24" aria-hidden="true"><path d="M12 2a10 10 0 1 0 0 20 10 10 0 0 0 0-20zm0 2c.9 1.2 1.6 2.6 2 4h-4c.4-1.4 1.1-2.8 2-4zM4.3 14a8 8 0 0 1 0-4h3.4a16 16 0 0 0 0 4zm.8 2h3c.3 1.3.8 2.5 1.5 3.6A8 8 0 0 1 5.1 16zm3-8h-3a8 8 0 0 1 4.5-3.6C8.9 5.5 8.4 6.7 8.1 8zM12 20c-.9-1.2-1.6-2.6-2-4h4c-.4 1.4-1.1 2.8-2 4zm2.3-6H9.7a14 14 0 0 1 0-4h4.6a14 14 0 0 1 0 4zm.1 5.6c.7-1.1 1.2-2.3 1.5-3.6h3a8 8 0 0 1-4.5 3.6zM16.3 14a16 16 0 0 0 0-4h3.4a8 8 0 0 1 0 4z"/></svg>
      </li>
    </ul>
  </section>

</main>
</body>
</html>
```